Stage Design Company Business Card

We are looking to step up up our business card design for our team.

We are a Full service Design and Consultation company for Stage and TV with an emphasis in Theatrical Lighting.

We like our materials to be clean and modern with solid colors free of patterns and gradients. Our brand consists of 4 primary colors Purple, Black, Grey, and White. Provided is our Word Mark as well as our Symbol Logo.

We would like our cards to leave an impression beyond the information, show our attention to design and detail, and make our marks an easily recognized feature (together or apart) for our clients.

We need a warm approachable comfortable feel for some clients, and a professional flair for the board member type clients.

Attached are our brand elements, and our existing cards to give a sense of our style and a glipse at the information we provide on our cards.

Target Market(s)

broad client base from church leaders to high school teachers and architects.

Industry/Entity Type

Business

Contact Information for Business Card

We format our phone number with periods not parenthesis or dashes. Information will be edited for each of our team members, and team member specific cards are not part of this scope, but rather a template so to speak.

Font styles to use
Sans Serif

Colors
6b449b
ffffff
000000
333333
aaaaaa

Requirements
Must have
• Wordmark and logo mark present (does not need to exist on the same side of card)
• Brand Colors,
• Name, Phone, Email, Address.
• Unique choices that make someone stop and take a second look
Nice to have
• It would be nice to somehow convey what we DO, as our brand name does not lend itself to this, outside of an obvious tagline though.....
• social media if not crowded. all of our handles match (instagram, twitter, facebook)
Should not have
• "clipart"

```html
<!DOCTYPE html>
<html lang="en">
<head>
<meta charset="utf-8">
<title>Halvorsen Stage – Business Card</title>
<link rel="stylesheet" href="https://fonts.googleapis.com/css2?family=Michroma&family=Raleway:wght@300&display=swap">
<style>
  :root {
    --backdrop: #d6c3a6;
    --card-purple: #37236b;
    --ink-white: #ffffff;
    --ink-soft: #c9bfe0;
    --card-shadow: rgba(40, 25, 10, 0.35);
  }
  * { margin: 0; padding: 0; box-sizing: border-box; }
  html, body {
    width: 1200px;
    height: 995px;
    overflow: hidden;
    background: var(--backdrop);
  }
  .sheet {
    width: 1200px;
    height: 995px;
    display: flex;
    justify-content: center;
    align-items: center;
    gap: 90px;
  }
  .card {
    width: 420px;
    height: 735px;
    background: var(--card-purple);
    color: var(--ink-white);
    box-shadow: 0 14px 30px var(--card-shadow);
    display: flex;
    flex-direction: column;
    align-items: center;
  }
  .card--front { justify-content: center; }
  .brand {
    display: flex;
    flex-direction: column;
    align-items: center;
    gap: 34px;
  }
  .brand__dot {
    width: 120px;
    height: 120px;
    border-radius: 50%;
    background: var(--ink-white);
  }
  .brand__name {
    font-family: "Michroma", sans-serif;
    font-size: 30px;
    letter-spacing: 0.22em;
    text-align: center;
    line-height: 1.5;
  }
  .brand__web {
    font-family: "Raleway", sans-serif;
    font-weight: 300;
    font-size: 20px;
    letter-spacing: 0.28em;
    color: var(--ink-soft);
    margin-top: -6px;
  }
  .card--back {
    justify-content: flex-start;
    padding-top: 170px;
    font-family: "Michroma", sans-serif;
    text-align: center;
  }
  .contact__name {
    font-size: 25px;
    letter-spacing: 0.1em;
    margin-bottom: 52px;
  }
  .contact__line {
    font-size: 20px;
    letter-spacing: 0.04em;
    margin-bottom: 54px;
  }
  .contact__email { font-size: 17px; }
  .contact__address {
    font-size: 19px;
    line-height: 1.45;
    letter-spacing: 0.06em;
  }
</style>
</head>
<body>
  <main class="sheet">
    <section class="card card--front">
      <div class="brand">
        <div class="brand__dot"></div>
        <p class="brand__name">HALVORSEN<br>STAGE</p>
        <p class="brand__web">HALVORSEN-S.COM</p>
      </div>
    </section>

    <section class="card card--back">
      <p class="contact__name">MARA K LINDEN</p>
      <p class="contact__line">555.014.2281</p>
      <p class="contact__line contact__email">mara@halvorsen-s.com</p>
      <p class="contact__address">412 E BIRCH AVE<br>HARLOW, AZ 85999</p>
    </section>
  </main>
</body>
</html>
```